Satchel & Sundial needs new business card design

I need a new business card design. I'm looking for out-of-the-box design which represents the freedom of being a location independent entrepreneur.
I offer coaching, retreats and trips.
I would like to see designs with and without the photo.
Colors I use are black (#000000), green (#25A796) and brown (#D7C38C)
Website satchelandsundial.example

Target Market(s)

location independent entrepreneurs, digital nomads, people looking to swap the 9 to 5 for a lifestyle business

Industry/Entity Type

Business

Contact Information for Business Card

Dorota Falkner
Your Lifestyle Business Coach, Retreat & Trip Leader
http://satchelandsundial.example
hello@satchelandsundial.example
Live a life you don't need a holiday from

Font styles to use
Serif
Sans Serif

Requirements
Must have
• One side should contain only the logo. I would also consider having the "Live a life you don't need a holiday from" on that side too (depending on how it looks)
• Please show both sides on the designs.

```html
<!DOCTYPE html>
<html lang="en">
<head>
<meta charset="utf-8">
<title>Satchel &amp; Sundial — Business Card</title>
<link rel="stylesheet" href="https://fonts.googleapis.com/css2?family=Open+Sans:wght@400;600;700&display=swap">
<style>
  :root {
    --ink: #231f20;
    --teal: #25a796;
    --paper: #ffffff;
    --backdrop: #e4e4e4;
    --type: "Open Sans", Arial, sans-serif;
  }
  * { box-sizing: border-box; margin: 0; padding: 0; }
  html, body {
    width: 1105px;
    height: 1200px;
    overflow: hidden;
    background: var(--backdrop);
    font-family: var(--type);
  }
  .card {
    position: absolute;
    left: 196px;
    width: 720px;
    height: 412px;
    background: var(--paper);
    overflow: hidden;
  }
  .card--front { top: 146px; }
  .card--back  { top: 602px; height: 410px; }

  .wordmark {
    position: absolute;
    color: var(--ink);
    font-weight: 600;
    white-space: nowrap;
    letter-spacing: 0.5px;
  }
  .card--front .wordmark {
    right: 40px;
    top: 62px;
    font-size: 44px;
  }
  .card--back .wordmark {
    left: 0;
    right: 0;
    top: 186px;
    text-align: center;
    font-size: 56px;
  }

  .name-band {
    position: absolute;
    left: 0;
    top: 200px;
    width: 427px;
    height: 112px;
  }
  .identity {
    position: absolute;
    left: 29px;
    top: 214px;
    color: var(--paper);
  }
  .identity__name {
    font-size: 25px;
    font-weight: 700;
    letter-spacing: 0.4px;
    line-height: 1.2;
    text-transform: uppercase;
  }
  .identity__role {
    font-size: 19px;
    line-height: 1.4;
  }

  .contact-bar {
    position: absolute;
    left: 0;
    right: 0;
    top: 312px;
    bottom: 0;
    background: var(--ink);
    color: var(--paper);
    font-size: 19px;
    display: flex;
    align-items: center;
    justify-content: space-between;
    padding: 0 34px 0 29px;
  }
  .contact-bar__item {
    display: flex;
    align-items: center;
    gap: 10px;
  }

  .social {
    position: absolute;
    top: 26px;
    right: 24px;
    display: flex;
    gap: 5px;
  }
  .social__tile {
    width: 25px;
    height: 25px;
    background: var(--teal);
  }

  .motto-bar {
    position: absolute;
    left: 0;
    right: 0;
    top: 348px;
    height: 41px;
    background: var(--ink);
    color: var(--teal);
    font-size: 18px;
    letter-spacing: 1.4px;
    text-transform: uppercase;
    display: flex;
    align-items: center;
    justify-content: center;
  }
</style>
</head>
<body>

  <section class="card card--front" aria-label="Business card front">
    <div class="wordmark">Satchel &amp; Sundial</div>

    <svg class="name-band" viewBox="0 0 427 112" aria-hidden="true">
      <polygon points="0,0 322,0 427,112 0,112" fill="#25a796"/>
    </svg>
    <div class="identity">
      <p class="identity__name">Dorota Falkner</p>
      <p class="identity__role">Your Lifestyle Business Coach</p>
      <p class="identity__role">Retreat &amp; Trip Leader</p>
    </div>

    <div class="contact-bar">
      <span class="contact-bar__item">
        <svg width="17" height="12" viewBox="0 0 17 12" aria-hidden="true">
          <rect x="0" y="0" width="17" height="12" fill="#25a796"/>
          <polyline points="0,0 8.5,7 17,0" fill="none" stroke="#231f20" stroke-width="1.4"/>
        </svg>
        hello@satchelandsundial.example
      </span>
      <span class="contact-bar__item">
        www.satchelandsundial.example
        <svg width="19" height="19" viewBox="0 0 20 20" aria-hidden="true">
          <circle cx="10" cy="10" r="9" fill="#25a796"/>
          <ellipse cx="10" cy="10" rx="4" ry="9" fill="none" stroke="#231f20" stroke-width="1.2"/>
          <line x1="1" y1="10" x2="19" y2="10" stroke="#231f20" stroke-width="1.2"/>
        </svg>
      </span>
    </div>
  </section>

  <section class="card card--back" aria-label="Business card back">
    <div class="social" aria-label="Social profiles">
      <span class="social__tile"></span>
      <span class="social__tile"></span>
      <span class="social__tile"></span>
    </div>
    <div class="wordmark">Satchel &amp; Sundial</div>
    <div class="motto-bar">Live a life you don't need a holiday from</div>
  </section>

</body>
</html>
```